Moxy Fen needs some awesome stationary

Do you have what it takes to get my brand? You either do or you don't, have a crack at a design and you my just win my business.

I don't want to waste your or my time, so put your creative genius on either a business card or envelope.

I however need a package of stationary that follows the same brand. I will message you to complete the remaining should I like your first submission.

Here is what I need, have a go!

Basically I need the following for my small business based in melbourne.
- Letterhead (printer ready and MS Word)
- Business Card
- Compliments Slip
- Envelope
- Proposal Cover Page (MS Word only)
- Presentation Folder
- Marbled Fox Cards
- Student Name Tent
- Index Cards
- Vell-Ka

I am establishing the brand and it must be modern, professional but also relaxed; that is not formal and not corporate. It represents a company are leaders, but small enough to care and operate like a bunch of friends. We are bringing people and conversations back to business, and turfing out all the bureaucracy and crazy and wasteful procedures. Its about "lets talk and figure it out together and find even better ways".

Target Market(s)

Mainly companies that build software products, but Agile practices are used in many other industries (even graphic design projects)

Industry/Entity Type

Information Technology

Font styles to use
Sans Serif

Colors
3176b5
aaaaaa

Requirements
Must have
• I like curves and circles and not boxes or rectangles.
• I want a colour rich design with my brand colours, but it must be balanced.
• I want more modern than traditional, but simple modern
Should not have
• Not corporate
• Please don't waste my time if your not going to think about it.
• Don't mess with my primary logo
• Don't change my colours
• Don't overlay logo on image

```html
<!DOCTYPE html>
<html lang="en">
<head>
<meta charset="utf-8">
<title>Moxy Fen — Letterhead</title>
<link href="https://fonts.googleapis.com/css2?family=Open+Sans:wght@400;700;800&display=swap" rel="stylesheet">
<style>
  :root {
    --brand-blue: #3176b5;
    --brand-grey: #aaaaaa;
    --accent-teal: #1a8fbf;
    --ink-soft: #7a7f88;
    --paper: #ffffff;
    --backdrop: #b7c0dc;
    --pattern-tint: #d9e9f7;
  }
  * { margin: 0; padding: 0; box-sizing: border-box; }
  html, body {
    width: 1200px; height: 784px; overflow: hidden;
    background: var(--backdrop);
    font-family: "Open Sans", sans-serif;
  }
  .letterhead {
    position: absolute; left: 338px; top: 22px;
    width: 523px; height: 740px;
    background: var(--paper);
    box-shadow: 0 2px 10px rgba(40, 50, 90, 0.18);
    overflow: hidden;
  }
  .brand {
    position: absolute; left: 30px; top: 44px;
    display: flex; align-items: center; gap: 8px;
  }
  .brand-dot {
    width: 34px; height: 34px; border-radius: 50%;
    background: var(--brand-blue);
  }
  .brand-name {
    font-weight: 800; font-size: 19px; color: var(--brand-blue);
    letter-spacing: 0.2px;
  }
  .pattern {
    position: absolute; border-radius: 40px;
  }
  .pattern-top {
    left: 100px; top: 8px; width: 140px; height: 100px;
    background: radial-gradient(ellipse at center, var(--pattern-tint) 0%, rgba(217,233,247,0) 72%);
  }
  .pattern-bottom {
    left: 370px; top: 560px; width: 150px; height: 170px;
    background: radial-gradient(ellipse at center, var(--pattern-tint) 0%, rgba(217,233,247,0) 72%);
  }
  .contact {
    position: absolute; left: 322px; top: 30px;
    font-size: 7px; line-height: 11px; color: var(--ink-soft);
  }
  .contact-company {
    font-weight: 800; font-size: 11px; line-height: 15px;
    color: var(--brand-blue);
  }
  .contact-line { display: flex; align-items: center; gap: 4px; white-space: nowrap; }
  .contact-icon {
    width: 6px; height: 6px; border-radius: 50%;
    background: var(--brand-blue); flex: none;
  }
  .watermark {
    position: absolute; left: 60px; top: 640px;
    display: flex; align-items: center; gap: 10px; opacity: 0.12;
  }
  .watermark-dot {
    width: 70px; height: 70px; border-radius: 50%; background: var(--brand-grey);
  }
  .watermark-name {
    font-weight: 800; font-size: 28px; color: var(--brand-grey);
  }
  .edge-band {
    position: absolute; left: 0; bottom: 0; height: 5px;
  }
  .edge-band-blue { width: 80%; background: var(--accent-teal); }
  .edge-band-grey { left: 80.6%; right: 0; background: #c9c9c9; }
</style>
</head>
<body>
  <main class="letterhead">
    <div class="pattern pattern-top" role="img" aria-label="Soft pattern of light blue rounded tiles"></div>

    <div class="brand">
      <span class="brand-dot"></span>
      <span class="brand-name">Moxy Fen</span>
    </div>

    <address class="contact">
      <div class="contact-company">Moxy Fen Pty Ltd</div>
      <div class="contact-line"><span class="contact-icon"></span>PO Box 4417, Larchmere, VIC 3921, Australia</div>
      <div class="contact-line"><span class="contact-icon"></span>1300 MOXYF <span class="contact-icon"></span>000 0000 0000</div>
      <div class="contact-line"><span class="contact-icon"></span>hello@moxyfen.example <span class="contact-icon"></span>www.moxyfen.example</div>
      <div class="contact-line">ABN No. 12 345 678 901</div>
    </address>

    <div class="watermark" aria-hidden="true">
      <span class="watermark-dot"></span>
      <span class="watermark-name">Moxy Fen</span>
    </div>

    <div class="pattern pattern-bottom" role="img" aria-label="Soft pattern of light blue rounded tiles"></div>

    <div class="edge-band edge-band-blue"></div>
    <div class="edge-band edge-band-grey"></div>
  </main>
</body>
</html>
```